Company web site

Looking for a full responsive(mobile friendly) wordpress implementation

Some material is in the website -- brelvanto.folionet.com

But looking for a template more consistent with the logo design, and more future looking.

Target Market(s)

Enterprise Clients

Industry/Entity Type

It Company

Font styles to use
Sans Serif

Colors
33a6d7
0255a3
0455a3
cfdeed
85abd2
3176b5

Requirements
Must have
• about, contact information, partner page, success stories, customer testimonials. links to social presence.
• pricing information

```html
<!DOCTYPE html>
<html lang="en">
<head>
<meta charset="utf-8">
<title>Brelvanto — Home</title>
<link rel="stylesheet" href="https://fonts.googleapis.com/css2?family=Questrial&family=Didact+Gothic&display=swap">
<style>
  :root {
    --ink: #111418;
    --ink-soft: #1c2128;
    --sky: #33a6d7;
    --sky-light: #cfdeed;
    --sky-mid: #85abd2;
    --sky-band: #a9cbe8;
    --navy: #0255a3;
    --steel: #3176b5;
    --panel: rgba(236, 244, 251, 0.82);
    --text-dark: #15191e;
    --white: #ffffff;
  }
  * { box-sizing: border-box; margin: 0; padding: 0; }
  html, body { width: 1200px; height: 612px; overflow: hidden; background: #e6e5e2; }
  .page {
    position: relative; width: 1200px; height: 612px; overflow: hidden;
    background: var(--ink); font-family: "Didact Gothic", sans-serif; color: var(--text-dark);
  }
  .header-sheen { position: absolute; inset: 0 0 auto 0; height: 170px; }
  .utility-links {
    position: absolute; top: 14px; right: 60px; display: flex;
    font-family: "Questrial", sans-serif; font-size: 11px; letter-spacing: 1px; color: var(--sky-light);
  }
  .utility-links span { padding: 0 12px; border-left: 1px solid var(--sky-light); }
  .utility-links span:first-child { border-left: none; }
  .brand {
    position: absolute; top: 44px; left: 330px; display: flex; align-items: center; gap: 24px;
  }
  .brand-dot { width: 66px; height: 66px; border-radius: 50%; background: var(--sky); }
  .brand-name {
    font-family: "Questrial", sans-serif; font-size: 88px; line-height: 1; letter-spacing: 2px; color: var(--sky);
  }
  .content-band {
    position: absolute; top: 168px; left: 0; width: 1200px; height: 332px;
    background: linear-gradient(120deg, var(--sky-light) 0%, var(--sky-band) 45%, var(--sky-mid) 100%);
  }
  .nav {
    position: absolute; top: 172px; left: 18px; display: flex; gap: 6px;
    font-family: "Questrial", sans-serif; font-size: 17px; letter-spacing: 2px;
  }
  .nav a {
    display: block; width: 184px; height: 26px; background: var(--ink);
    border-bottom: 2px solid var(--sky); transform: skewX(-22deg);
    color: var(--sky); text-decoration: none;
  }
  .nav a span { display: block; transform: skewX(22deg); padding: 3px 0 0 22px; }
  .content-panel {
    position: absolute; top: 226px; left: 30px; width: 700px; height: 230px;
    background: var(--panel); clip-path: polygon(0 0, 100% 6%, 100% 100%, 0 94%);
  }
  .page-title {
    position: absolute; top: 236px; left: 48px;
    font-family: "Questrial", sans-serif; font-weight: 400; font-size: 62px; letter-spacing: 3px; color: var(--text-dark);
  }
  .intro { position: absolute; top: 318px; left: 50px; width: 600px; font-size: 13px; line-height: 1.35; }
  .intro p + p { margin-top: 18px; }
  .footer { position: absolute; top: 500px; left: 0; width: 1200px; height: 112px; background: var(--ink); }
  .social { position: absolute; top: 24px; left: 50px; display: flex; gap: 16px; }
  .social a {
    display: flex; align-items: center; gap: 6px; font-family: "Questrial", sans-serif;
    font-size: 12px; color: var(--white); text-decoration: none;
  }
  .social a i { display: block; width: 18px; height: 18px; background: var(--white); border-radius: 2px; }
  .site-address {
    position: absolute; right: 40px; bottom: 14px; font-family: "Questrial", sans-serif;
    font-size: 11px; letter-spacing: 1px; color: var(--steel);
  }
</style>
</head>
<body>
<div class="page">
  <svg class="header-sheen" viewBox="0 0 1200 170" preserveAspectRatio="none" aria-hidden="true">
    <polygon points="0,0 520,0 380,170 0,170" fill="#1a1f26"/>
    <polygon points="760,0 1200,0 1200,170 980,170" fill="#181c22"/>
  </svg>

  <nav class="utility-links">
    <span>LOGIN</span><span>SUPPORT</span><span>CONTACT</span><span>PRIVACY POLICY</span>
  </nav>

  <div class="brand">
    <div class="brand-dot"></div>
    <div class="brand-name">Brelvanto</div>
  </div>

  <div class="content-band"></div>

  <nav class="nav">
    <a href="#"><span>HOME</span></a>
    <a href="#"><span>PLATFORM</span></a>
    <a href="#"><span>PARTNERS</span></a>
    <a href="#"><span>BLOG</span></a>
    <a href="#"><span>ABOUT</span></a>
    <a href="#"><span>CONTACT</span></a>
  </nav>

  <div class="content-panel"></div>
  <h1 class="page-title">HOME</h1>
  <div class="intro">
    <p>Brelvanto is company which provides specialized offerings in IoT domain. Based in the heart of the Silicon Valley, California. Brelvanto is built on decades of experience and knowledge.</p>
    <p>Brelvanto CX IoT platform for OEM's is designed to ease the transition of Product companies from selling unconnected products, into providing service for connected devices.</p>
  </div>

  <footer class="footer">
    <div class="social">
      <a href="#"><i></i>Profile</a>
      <a href="#"><i></i>Page</a>
      <a href="#"><i></i>Feed</a>
    </div>
    <div class="site-address">BRELVANTO.FOLIONET.COM</div>
  </footer>
</div>
</body>
</html>
```